Logo and Card design for KRV Home Solutions LLC

I need an edgier logo and business card designs. Current logo attached. I like the colors below. I would like the logo to incorporate a home in the design.
Title = Principal-Acquisitions
Email:KRVHOMESOLUTIONS@fernmail.example
555-214-0937
facebook
IG
2 sided business card with the front being contact info a slogan about selling a home fast. The back incorporating What we do. Buy houses, land, or commercial property as is. We find solutions to make the process of selling simple and fair.

Target Market(s)

Motivated house sellers.

Industry/Entity Type

Business

Contact Information for Business Card

Who we are: We are a Faith based Real Estate Investment Company. We pay cash for homes in any condition and can close quick. Whatever the reason you need to sell fast, we can help. We believe in creating win-win solutions to help you in your time of need. We care! We can help!

Logo Text

KRV Home Solutions LLC

Font styles to use
Sans Serif

Colors
33a6d7
0355a3
85abd2
cee9f5
9d9d9d
b2b2b2
ffffff

Requirements
Must have
• Old logo attached. I want something edgier.
• Company name, phone number, description on the back of what we can do. Pay all cash. Buy in as is condition. No fees,Commisions or closing costs.Close quick. No hassles with solutions to meet your unique situation.
• Call today for an offer within 24 hours.

```html
<!DOCTYPE html>
<html lang="en">
<head>
<meta charset="utf-8">
<title>KRV Home Solutions – Business Card</title>
<link href="https://fonts.googleapis.com/css2?family=Roboto:wght@400;500;700&family=Roboto+Condensed:wght@400;700&display=swap" rel="stylesheet">
<style>
  :root {
    --navy: #1f3a78;
    --gray-text: #555555;
    --gray-mid: #6b6b6b;
    --white: #ffffff;
    --paper: #f3f3f3;
    --stage: #2b2b2b;
    --photo-light: #e4eef6;
    --photo-mid: #c9d9e6;
    --photo-warm: #d7d4cd;
  }
  * { margin: 0; padding: 0; box-sizing: border-box; }
  html, body { width: 1200px; height: 960px; overflow: hidden; }
  body {
    position: relative;
    background: var(--stage);
    font-family: "Roboto", Arial, sans-serif;
  }
  .card {
    position: absolute;
    width: 600px;
    height: 343px;
    overflow: hidden;
  }
  /* Front */
  .card--front { left: 314px; top: 113px; background: var(--photo-light); }
  .front-photo {
    position: absolute; left: 0; top: 0; width: 600px; height: 259px;
    background:
      linear-gradient(90deg, rgba(240,246,251,0.92) 0%, rgba(240,246,251,0.6) 45%, rgba(240,246,251,0.1) 100%),
      linear-gradient(180deg, var(--photo-mid) 0%, var(--photo-warm) 65%, #b9c6b5 100%);
  }
  .brand-name {
    position: absolute; left: 35px; top: 34px;
    color: var(--navy); font-weight: 700; line-height: 1;
  }
  .brand-name__main { display: block; font-size: 40px; letter-spacing: 0.5px; }
  .brand-name__sub { display: block; font-size: 22px; margin: 12px 0 0 46px; letter-spacing: 0.5px; }
  .person {
    position: absolute; left: 34px; top: 130px;
  }
  .person__name {
    font-family: "Roboto Condensed", Arial, sans-serif;
    font-weight: 700; font-size: 26px; color: var(--navy); line-height: 1;
  }
  .person__title { font-size: 16px; color: var(--gray-mid); margin-top: 5px; font-weight: 500; }
  .contact { position: absolute; left: 35px; top: 184px; list-style: none; }
  .contact__item {
    display: flex; align-items: center; gap: 8px;
    font-size: 15px; color: var(--gray-text); height: 19px;
  }
  .contact__icon { width: 14px; height: 14px; fill: var(--navy); }
  .slogan-band {
    position: absolute; left: 0; top: 259px; width: 600px; height: 84px;
    background: var(--navy);
    color: var(--white);
    font-family: "Roboto Condensed", Arial, sans-serif;
    font-size: 15px; line-height: 18.5px; text-align: center;
    padding-top: 16px;
  }
  /* Back */
  .card--back { left: 311px; top: 472px; background: var(--paper); text-align: center; }
  .back-brand {
    position: absolute; left: 0; right: 0; top: 92px;
    color: var(--navy); font-weight: 700; font-size: 28px; line-height: 1;
    letter-spacing: 0.5px;
  }
  .info { position: absolute; left: 0; right: 0; top: 170px; }
  .info__heading {
    font-family: "Roboto Condensed", Arial, sans-serif;
    font-weight: 700; font-size: 16px; color: var(--navy); line-height: 20px;
  }
  .info__text { font-size: 15px; color: var(--gray-text); line-height: 18px; }
  .info__heading--second { margin-top: 11px; }
</style>
</head>
<body>
  <section class="card card--front">
    <div class="front-photo" role="img" aria-label="Photo of a family outside a modern two-storey house under a tree"></div>
    <div class="brand-name">
      <span class="brand-name__main">KRV HOME</span>
      <span class="brand-name__sub">SOLUTIONS</span>
    </div>
    <div class="person">
      <div class="person__name">JORDAN REYES</div>
      <div class="person__title">Principal-Acquisitions</div>
    </div>
    <ul class="contact">
      <li class="contact__item">
        <svg class="contact__icon" viewBox="0 0 24 24"><path d="M6.6 10.8a15.1 15.1 0 0 0 6.6 6.6l2.2-2.2a1 1 0 0 1 1-.25 11.4 11.4 0 0 0 3.6.57 1 1 0 0 1 1 1V20a1 1 0 0 1-1 1A17 17 0 0 1 3 4a1 1 0 0 1 1-1h3.5a1 1 0 0 1 1 1c0 1.25.2 2.45.57 3.57a1 1 0 0 1-.25 1z"/></svg>
        555-214-0937
      </li>
      <li class="contact__item">
        <svg class="contact__icon" viewBox="0 0 24 24"><path d="M2 5h20v14H2z M4 7v.4l8 5 8-5V7l-8 5z" fill-rule="evenodd"/></svg>
        KRVHOMESOLUTIONS@fernmail.example
      </li>
      <li class="contact__item">
        <svg class="contact__icon" viewBox="0 0 24 24"><circle cx="12" cy="12" r="10"/><path d="M7 8c2 0 3 1 3 3s2 2 2 4-1 3-1 5M15 4c0 2 1 3 3 3M17 13c1 0 2 1 2 3" stroke="#e4eef6" stroke-width="1.6" fill="none"/></svg>
        KRVHOMESOLUTIONS.example
      </li>
    </ul>
    <p class="slogan-band">
      Pay all cash. Buy in as is condition.• No fees,Commisions or closing costs.<br>
      Close quick. No hassles with solutions to meet your unique situation.<br>
      Call today for an offer within 24 hours.
    </p>
  </section>

  <section class="card card--back">
    <div class="back-brand">KRV HOME SOLUTIONS</div>
    <div class="info">
      <h2 class="info__heading">WHO WE ARE</h2>
      <p class="info__text">We are a Faith based Real Estate Investment Company. We pay cash for<br>homes in any condition and can close quick. Whatever the reason you need<br>to sell fast, we can help. We believe in creating win-win solutions to help</p>
      <h2 class="info__heading info__heading--second">WHAT WE DO</h2>
      <p class="info__text">Buy houses, land, or commercial property as is.<br>We find solutions to make the process of selling simple and fair.</p>
    </div>
  </section>
</body>
</html>
```